Harborline Renewal Business Card Design

Professional and clean design. The design colors should flow with the logo. Two-sided card with the website on the back which is:

www.HarborlineRenewal.example.

"Specializing in Water Damage Restoration"

On the front I need the name, email, phone, and logo.

Name: Darnell Quisby
Email: Darnell@HarborlineRenewal.example
Phone: 555-318-2046 for now

I only have the Preview and Thumbnail right now but should have the source files uploaded within a day or two.

Target Market(s)

Flood victims, home owners with water damage from busted pipes etc...

Industry/Entity Type

Business

Contact Information for Business Card

Name: Darnell Quisby

Font styles to use
Serif
Sans Serif

Requirements
Must have
• Business Card Details Info

```html
<!DOCTYPE html>
<html lang="en">
<head>
<meta charset="utf-8">
<title>Harborline Renewal Business Card</title>
<link href="https://fonts.googleapis.com/css2?family=Cinzel:wght@500;600&family=Source+Sans+3:wght@400&display=swap" rel="stylesheet">
<style>
  :root {
    --page-bg: #202020;
    --card-white: #ffffff;
    --brand-blue: #2a96d6;
    --brand-light: #5bc0ee;
    --text-blue: #2288cc;
    --rule-blue: #5bc0ee;
    --serif: "Cinzel", Georgia, serif;
    --sans: "Source Sans 3", Arial, sans-serif;
  }
  html, body {
    margin: 0; padding: 0;
    width: 1200px; height: 741px;
    overflow: hidden;
    background: var(--page-bg);
  }
  .canvas { position: relative; width: 1200px; height: 741px; }
  .card {
    position: absolute;
    top: 236px;
    width: 494px; height: 282px;
    background: var(--card-white);
    overflow: hidden;
  }
  .card--back { left: 86px; }
  .card--front { left: 619px; }

  .brand-dot {
    position: absolute;
    border-radius: 50%;
    background: var(--brand-blue);
  }
  .brand-name {
    position: absolute;
    left: 0; right: 0;
    margin: 0;
    text-align: center;
    font-family: var(--serif);
    font-weight: 600;
    color: var(--text-blue);
    white-space: nowrap;
    letter-spacing: 0.5px;
  }
  .tagline {
    position: absolute;
    left: 0; right: 0;
    margin: 0;
    text-align: center;
    font-family: var(--sans);
    font-size: 13px;
    color: var(--text-blue);
    white-space: nowrap;
  }

  /* back side */
  .card--back .brand-dot { left: 213px; top: 55px; width: 70px; height: 70px; }
  .card--back .brand-name { top: 136px; font-size: 26px; }
  .card--back .tagline { top: 190px; }
  .web-rule {
    position: absolute;
    top: 248px;
    height: 1px;
    background: var(--rule-blue);
  }
  .web-rule--left { left: 0; width: 138px; }
  .web-rule--right { left: 358px; right: 0; }
  .web-address {
    position: absolute;
    top: 239px; left: 138px; width: 220px;
    margin: 0;
    text-align: center;
    font-family: var(--sans);
    font-size: 13px;
    color: var(--text-blue);
  }

  /* front side */
  .swoosh { position: absolute; inset: 0; width: 100%; height: 100%; }
  .front-brand { position: absolute; left: 20px; top: 0; width: 244px; height: 170px; }
  .card--front .brand-dot { left: 89px; top: 26px; width: 66px; height: 66px; }
  .card--front .brand-name { top: 100px; font-size: 22px; }
  .card--front .tagline { top: 150px; font-size: 12px; }

  .holder {
    position: absolute;
    right: 17px; top: 176px;
    margin: 0;
    font-family: var(--serif);
    font-weight: 600;
    font-size: 19px;
    color: var(--card-white);
    letter-spacing: 0.5px;
  }
  .contact-list {
    position: absolute;
    right: 17px; top: 208px;
    margin: 0; padding: 0;
    list-style: none;
    font-family: var(--sans);
    font-size: 14px;
    color: var(--card-white);
    text-align: right;
  }
  .contact-list li {
    display: flex; align-items: center; justify-content: flex-end;
    gap: 5px; height: 18.5px;
  }
  .contact-icon {
    width: 14px; height: 14px;
    background: var(--card-white);
    display: inline-flex; align-items: center; justify-content: center;
  }
  .contact-icon svg { width: 11px; height: 11px; }
</style>
</head>
<body>
<div class="canvas">

  <section class="card card--back" aria-label="Card back">
    <span class="brand-dot" aria-hidden="true"></span>
    <h1 class="brand-name">Harborline Renewal</h1>
    <p class="tagline">Specializing in Water Damage Restoration</p>
    <span class="web-rule web-rule--left"></span>
    <p class="web-address">www.HarborlineRenewal.example</p>
    <span class="web-rule web-rule--right"></span>
  </section>

  <section class="card card--front" aria-label="Card front">
    <svg class="swoosh" viewBox="0 0 599 342" preserveAspectRatio="none" aria-hidden="true">
      <path d="M0 252 C150 262 340 228 475 130 C360 218 180 292 0 306 Z" fill="var(--brand-light)"/>
      <path d="M599 0 L594 0 C500 120 300 268 0 312 L0 342 L599 342 Z" fill="var(--brand-blue)"/>
      <path d="M594 0 C500 120 300 268 0 312" fill="none" stroke="#ffffff" stroke-width="2"/>
    </svg>

    <div class="front-brand">
      <span class="brand-dot" aria-hidden="true"></span>
      <h2 class="brand-name">Harborline Renewal</h2>
      <p class="tagline">Specializing in Water Damage Restoration</p>
    </div>

    <p class="holder">Darnell Quisby</p>
    <ul class="contact-list">
      <li>555-318-2046
        <span class="contact-icon"><svg viewBox="0 0 12 12"><path d="M2 4 Q6 1 10 4 L9 5.5 L7.5 4.8 L7.5 4 Q6 3.5 4.5 4 L4.5 4.8 L3 5.5 Z M3 6.5 H9 L9.5 10 H2.5 Z" fill="var(--brand-blue)"/></svg></span>
      </li>
      <li>Darnell@HarborlineRenewal.example
        <span class="contact-icon"><svg viewBox="0 0 12 12"><rect x="1" y="2.5" width="10" height="7" fill="none" stroke="var(--brand-blue)" stroke-width="1.2"/><path d="M1 2.5 L6 7 L11 2.5 M1 9.5 L4.5 6 M11 9.5 L7.5 6" fill="none" stroke="var(--brand-blue)" stroke-width="1"/></svg></span>
      </li>
      <li>www.HarborlineRenewal.example
        <span class="contact-icon"><svg viewBox="0 0 12 12"><circle cx="6" cy="6" r="4.6" fill="none" stroke="var(--brand-blue)" stroke-width="1"/><ellipse cx="6" cy="6" rx="2" ry="4.6" fill="none" stroke="var(--brand-blue)" stroke-width="0.9"/><path d="M1.4 6 H10.6 M2 3.8 H10 M2 8.2 H10" stroke="var(--brand-blue)" stroke-width="0.8"/></svg></span>
      </li>
    </ul>
  </section>

</div>
</body>
</html>
```